Business Card Design (NEW FILES)

ATTENTION: New vector files are available. Please update your design to reflect/use the new (better resolution) logo images.

Seeking a unique and professional business card design for a commercial drone photography/videography business. The layout should feature
the logo (attached) and include the following information:
Owen Tarrick
614-502-7738
www.skylarkreelworks.example
NRD Certified Remote Pilot

Owen Tarrick

```html
<!DOCTYPE html>
<html lang="en">
<head>
<meta charset="utf-8">
<title>Skylark Reelworks – Business Card</title>
<link rel="stylesheet" href="https://fonts.googleapis.com/css2?family=Open+Sans:wght@400;600;700&display=swap">
<style>
  :root {
    --page-bg: #e6e2dc;
    --card-navy-light: #2c3060;
    --card-navy: #1b1c48;
    --card-navy-deep: #101036;
    --accent-orange: #d0743a;
    --text-light: #cfcbd3;
    --text-soft: #b9b6c4;
  }
  * { box-sizing: border-box; margin: 0; padding: 0; }
  html, body {
    width: 1200px; height: 1046px; overflow: hidden;
    background: var(--page-bg);
    font-family: "Open Sans", Arial, sans-serif;
  }
  .stage {
    width: 1200px; height: 1046px;
    display: flex; align-items: center; justify-content: center;
  }
  .business-card {
    position: relative;
    width: 1000px; height: 546px;
    border-radius: 36px;
    overflow: hidden;
    background:
      radial-gradient(ellipse at 12% 28%, var(--card-navy-light) 0%, transparent 55%),
      radial-gradient(ellipse at 20% 85%, #2a2d58 0%, transparent 50%),
      linear-gradient(120deg, var(--card-navy) 0%, var(--card-navy-deep) 55%, var(--card-navy) 100%);
    box-shadow: 0 18px 40px rgba(0,0,0,.25);
  }
  .brand {
    position: absolute; left: 44px; top: 52px;
    display: flex; align-items: center; gap: 14px;
  }
  .brand-dot {
    width: 30px; height: 30px; border-radius: 50%;
    background: var(--accent-orange);
  }
  .brand-name {
    font-size: 34px; font-weight: 400; letter-spacing: 2px;
    color: var(--text-light); text-transform: uppercase;
  }
  .owner-block {
    position: absolute; right: 43px; top: 42px;
    text-align: right;
  }
  .owner-name {
    font-size: 42px; font-weight: 700; line-height: 1.05;
    color: var(--accent-orange); letter-spacing: .5px;
  }
  .owner-title {
    font-size: 21px; font-weight: 400; color: var(--text-light);
    margin-top: 6px; letter-spacing: .5px;
  }
  .accent-bar {
    position: absolute; right: 0; top: 42px;
    width: 24px; height: 83px;
    background: var(--accent-orange);
  }
  .credentials {
    position: absolute; left: 42px; top: 328px;
    font-size: 22px; line-height: 32px; color: var(--text-soft);
    letter-spacing: .4px;
  }
  .contact-list {
    position: absolute; left: 40px; top: 418px;
    list-style: none;
  }
  .contact-item {
    display: flex; align-items: center; gap: 14px;
    height: 33px;
    font-size: 22px; color: var(--text-soft); letter-spacing: .4px;
  }
  .contact-icon { width: 24px; height: 24px; flex: none; }
</style>
</head>
<body>
<main class="stage">
  <section class="business-card" aria-label="Skylark Reelworks business card">
    <div class="brand">
      <span class="brand-dot"></span>
      <span class="brand-name">Skylark Reelworks</span>
    </div>

    <div class="owner-block">
      <p class="owner-name">Owen Tarrick</p>
      <p class="owner-title">Owner</p>
    </div>
    <span class="accent-bar"></span>

    <div class="credentials">
      <p>NRD Certified Remote Pilot</p>
      <p>Fully Insured</p>
    </div>

    <ul class="contact-list">
      <li class="contact-item">
        <svg class="contact-icon" viewBox="0 0 24 24" aria-hidden="true">
          <path fill="#d0743a" d="M6.6 10.8a15.2 15.2 0 0 0 6.6 6.6l2.2-2.2c.3-.3.7-.4 1-.2 1.1.4 2.3.6 3.6.6.6 0 1 .4 1 1V20c0 .6-.4 1-1 1A17 17 0 0 1 3 4c0-.6.4-1 1-1h3.5c.6 0 1 .4 1 1 0 1.3.2 2.5.6 3.6.1.3 0 .7-.2 1z"/>
        </svg>
        <span>614-502-7738</span>
      </li>
      <li class="contact-item">
        <svg class="contact-icon" viewBox="0 0 24 24" aria-hidden="true">
          <circle cx="12" cy="12" r="10" fill="#d0743a"/>
          <path fill="none" stroke="#1b1c48" stroke-width="1.4" d="M2 12h20M12 2c3 3 3 17 0 20M12 2c-3 3-3 17 0 20"/>
        </svg>
        <span>www.skylarkreelworks.example</span>
      </li>
      <li class="contact-item">
        <svg class="contact-icon" viewBox="0 0 24 24" aria-hidden="true">
          <rect x="2" y="6" width="20" height="14" rx="1.5" fill="#d0743a"/>
          <path fill="none" stroke="#1b1c48" stroke-width="1.5" d="M2.5 7l9.5 7 9.5-7"/>
        </svg>
        <span>info@skylarkreelworks.example</span>
      </li>
    </ul>
  </section>
</main>
</body>
</html>
```